Walk Beside The River

Business Card design

Target Market(s)

People who require support in the commnity

Industry/Entity Type

Mental Health Support

Contact Information for Business Card

Mental Health Support Rosalind Tavener walkbesidetheriver@mailcove.com.au 0481 637 092 PO Box 926 Willowmere QLD 4573

Colors
6B429C
8869AF
B7A5CE
E3DAEB
F3F0F8

Requirements
Must have
• Logo & details listed above
Should not have
• No red or orange

```html
<!DOCTYPE html>
<html lang="en">
<head>
<meta charset="utf-8">
<title>Walk Beside The River – Business Card</title>
<link href="https://fonts.googleapis.com/css2?family=Inter:wght@400;700&display=swap" rel="stylesheet">
<style>
  :root {
    --purple: #6B429C;
    --purple-deep: #5a3196;
    --purple-mid: #8869AF;
    --lavender: #B7A5CE;
    --mist: #E3DAEB;
    --paper: #F3F0F8;
    --card-white: #f1f1ef;
    --text-grey: #6a6a6e;
    --backdrop: #dcdde0;
  }
  * { box-sizing: border-box; margin: 0; padding: 0; }
  html, body { width: 1200px; height: 1051px; overflow: hidden; }
  body {
    background: var(--backdrop);
    font-family: "Inter", Arial, sans-serif;
    display: flex;
    flex-direction: column;
    align-items: center;
    justify-content: center;
    gap: 60px;
  }
  .card {
    width: 640px;
    height: 390px;
    border-radius: 4px;
    box-shadow: 0 18px 40px rgba(0,0,0,0.18);
    position: relative;
  }
  .card--front {
    background: var(--card-white);
    border-bottom: 4px solid var(--purple-deep);
    display: flex;
    align-items: center;
    padding: 0 36px 0 44px;
  }
  .brand {
    width: 190px;
    flex: none;
    display: flex;
    flex-direction: column;
    align-items: center;
    gap: 16px;
  }
  .brand__dot {
    width: 130px;
    height: 130px;
    border-radius: 50%;
    background: var(--purple);
  }
  .brand__name {
    color: var(--purple);
    font-weight: 700;
    font-size: 16px;
    line-height: 1.3;
    text-align: center;
    letter-spacing: 0.04em;
  }
  .divider {
    width: 2px;
    height: 190px;
    flex: none;
    background: var(--purple);
    margin: 0 28px 0 30px;
  }
  .details { display: flex; flex-direction: column; min-width: 0; }
  .details__role, .details__name {
    color: var(--purple);
    font-weight: 700;
    font-size: 22px;
    line-height: 1.2;
  }
  .details__address {
    margin-top: 14px;
    color: var(--text-grey);
    font-size: 16px;
    line-height: 1.4;
  }
  .contact {
    margin-top: 12px;
    display: flex;
    flex-direction: column;
    gap: 4px;
  }
  .contact__row {
    display: flex;
    align-items: center;
    gap: 8px;
    color: var(--text-grey);
    font-size: 16px;
    white-space: nowrap;
  }
  .contact__row--email { font-size: 15px; }
  .contact__icon { width: 14px; height: 14px; flex: none; fill: var(--purple); }
  .card--back {
    background: var(--purple-deep);
    display: flex;
    flex-direction: column;
    align-items: center;
    justify-content: center;
    gap: 18px;
  }
  .card--back .brand__dot {
    width: 150px;
    height: 150px;
    background: var(--purple);
    border: 2px solid var(--mist);
  }
  .card--back .brand__name { color: var(--paper); font-size: 18px; }
</style>
</head>
<body>
  <section class="card card--front">
    <div class="brand">
      <div class="brand__dot"></div>
      <p class="brand__name">Walk Beside The River</p>
    </div>
    <div class="divider"></div>
    <div class="details">
      <p class="details__role">Mental Health Support</p>
      <p class="details__name">Rosalind Tavener</p>
      <p class="details__address">PO Box 926<br>Willowmere QLD 4573</p>
      <div class="contact">
        <p class="contact__row">
          <svg class="contact__icon" viewBox="0 0 24 24" aria-hidden="true"><path d="M6.6 10.8a15.1 15.1 0 0 0 6.6 6.6l2.2-2.2a1 1 0 0 1 1-.25 11.4 11.4 0 0 0 3.6.57 1 1 0 0 1 1 1V20a1 1 0 0 1-1 1A17 17 0 0 1 3 4a1 1 0 0 1 1-1h3.5a1 1 0 0 1 1 1c0 1.25.2 2.45.57 3.6a1 1 0 0 1-.25 1z"/></svg>
          0481 637 092
        </p>
        <p class="contact__row contact__row--email">
          <svg class="contact__icon" viewBox="0 0 24 24" aria-hidden="true"><path d="M2 5h20v14H2z"/><path d="M2 6l10 7.5L22 6" fill="none" stroke="var(--card-white)" stroke-width="1.6"/></svg>
          walkbesidetheriver@mailcove.com.au
        </p>
      </div>
    </div>
  </section>

  <section class="card card--back">
    <div class="brand__dot"></div>
    <p class="brand__name">Walk Beside The River</p>
  </section>
</body>
</html>
```